Business Card Design and Logo Needed

I need Business Cards and a Logo for my website and public speaking business which can be found at: www.corvina-lett.example

I'm looking for creative and unique ideas. Some business cards I've found online that I like can be found at:
http://gigbarrow.example/general/18-smokin-hot-business-card-designs/

and at

http://www.plumquarry.example/2009/04/50-creative-business-cards-of-50-graphic-designers/

```html
<!DOCTYPE html>
<html lang="en">
<head>
<meta charset="utf-8">
<title>Corvina Lett — Business Card</title>
<link rel="stylesheet" href="https://fonts.googleapis.com/css2?family=Source+Sans+3:ital,wght@0,300;0,400;1,300;1,400;1,600;1,700&display=swap">
<style>
  :root {
    --bark: #433610;
    --bark-ink: #4a3b12;
    --sand: #d9d2bc;
    --tan: #9b8f6e;
    --paper: #ffffff;
  }
  * { box-sizing: border-box; margin: 0; padding: 0; }
  html, body {
    width: 1200px;
    height: 900px;
    overflow: hidden;
    background: var(--paper);
    font-family: "Source Sans 3", "Myriad Pro", sans-serif;
  }
  .canvas {
    position: relative;
    width: 1200px;
    height: 900px;
  }
  .card {
    position: absolute;
    left: 220px;
    width: 758px;
  }
  .card-front {
    top: 36px;
    height: 378px;
    background: var(--bark);
    border-top-left-radius: 112px;
  }
  .card-back {
    top: 482px;
    height: 380px;
    background: var(--paper);
    border: 3px solid var(--bark);
    border-top-right-radius: 124px;
    color: var(--bark-ink);
  }
  .brand-name {
    position: absolute;
    left: 42px;
    top: 220px;
    font-size: 44px;
    font-weight: 300;
    line-height: 1;
    color: var(--paper);
    letter-spacing: 0.5px;
  }
  .tagline {
    position: absolute;
    left: 42px;
    top: 320px;
    font-size: 26px;
    font-weight: 300;
    line-height: 1.2;
    color: var(--sand);
  }
  .name {
    position: absolute;
    right: 55px;
    top: 62px;
    font-size: 92px;
    font-style: italic;
    font-weight: 300;
    line-height: 1;
    letter-spacing: -1px;
    white-space: nowrap;
  }
  .name .surname { font-weight: 600; }
  .role {
    position: absolute;
    right: 55px;
    top: 160px;
    font-size: 18px;
    font-style: italic;
    font-weight: 300;
    line-height: 1.2;
    color: var(--tan);
  }
  .phone {
    position: absolute;
    right: 55px;
    top: 258px;
    font-size: 26px;
    font-style: italic;
    font-weight: 700;
    line-height: 1.2;
  }
  .contact-line {
    position: absolute;
    right: 55px;
    top: 304px;
    display: flex;
    gap: 44px;
    font-size: 26px;
    font-style: italic;
    font-weight: 300;
    line-height: 1.2;
    white-space: nowrap;
  }
</style>
</head>
<body>
  <main class="canvas">
    <section class="card card-front" aria-label="Card front">
      <p class="brand-name">corvina lett</p>
      <p class="tagline">wonder. explore. dream. achieve</p>
    </section>

    <section class="card card-back" aria-label="Card back">
      <h1 class="name">corvina<span class="surname">lett</span></h1>
      <p class="role">public speaker</p>
      <p class="phone">0142 808 315</p>
      <p class="contact-line">
        <span class="email">corvina@corvina-lett.example</span>
        <span class="website">corvina-lett.example</span>
      </p>
    </section>
  </main>
</body>
</html>
```